Theme and starter template for small business powerpoint deck

We are starting a technology consulting company and would like to have a powerpoint/google slide theme and initial template. We are more concerned with the theme/colors at this point. Initial template can be pretty simple. We would want a cover slide, agenda slide, some content slides including text content, image content, a combination of both, etc. A closing slide. we have included jpg files of our logo, let us know if you would prefer eps/vector. I assume you may want exact color data as well?

Target Market(s)

Technology and Customer Experience Leadership at companies with 25 or more employees

Industry/Entity Type

Technology Consulting

Font styles to use
Sans Serif

Colors
0054AA
0677BA
7BADD7
CADEEF
E8F1F8

Requirements
Must have
• I have attached JPG and EPS and vector files to project. I would like to stay with those colors but open to slight variation if recommended.

```html
<!DOCTYPE html>
<html lang="en">
<head>
<meta charset="utf-8">
<title>Vantoris – Deck Theme</title>
<link rel="stylesheet" href="https://fonts.googleapis.com/css2?family=Open+Sans:wght@600;700;800&family=Roboto:wght@400;500;700&display=swap">
<style>
:root{
  --blue-deep:#0054AA;
  --blue:#0677BA;
  --blue-soft:#7BADD7;
  --blue-pale:#CADEEF;
  --blue-mist:#E8F1F8;
  --red:#D2393D;
  --ink:#1d1d1f;
  --text:#5a5a5a;
  --grey:#7d7f80;
  --track:#e1e1e1;
  --stage:#b3b3b3;
  --white:#ffffff;
}
*{box-sizing:border-box;margin:0;padding:0}
html,body{width:1032px;height:1200px;overflow:hidden;background:var(--stage)}
body{font-family:"Roboto",Arial,sans-serif;color:var(--ink)}
.sheet{position:absolute;left:0;top:0;width:1781px;height:2072px;transform:scale(.57945);transform-origin:0 0}
.slide{position:absolute;width:765px;height:430px;background:var(--white);overflow:hidden}
.col-l{left:80px}.col-r{left:937px}
.row-1{top:82px}.row-2{top:575px}.row-3{top:1067px}.row-4{top:1560px}
.abs{position:absolute}
.heading{font-family:"Open Sans",Arial,sans-serif;font-weight:700;color:var(--ink);letter-spacing:.3px}
.heading-center{position:absolute;left:0;width:100%;text-align:center;font-size:24px}
.rule{position:absolute;height:2px;background:#9c9c9c}
.rule-center{left:352px;width:60px}
.brand{font-family:"Open Sans",Arial,sans-serif;font-weight:700;font-size:19px;letter-spacing:1px;color:var(--ink);white-space:nowrap}
.brand-mark{display:inline-block;width:9px;height:9px;background:var(--red);margin-left:5px;vertical-align:1px}
.photo{position:absolute}

/* cover */
.cover-brand{left:0;width:372px;top:110px;text-align:center}
.cover-title{left:0;width:372px;top:150px;text-align:center;font-size:25px}
.cover-lead{left:0;width:372px;top:188px;text-align:center;font-size:11px;line-height:20px;color:#333}
.cover-line{left:100px;top:244px;width:160px;height:1px;background:#999}
.cover-url{left:0;width:360px;top:263px;text-align:center;font-size:12.5px;color:var(--blue)}
.social{position:absolute;top:294px;width:24px;height:24px;border-radius:50%;background:var(--blue)}

/* agenda */
.agenda-panel{left:0;top:0;width:228px;height:430px;background:var(--blue-deep)}
.agenda-brand{left:33px;top:32px;color:var(--white)}
.agenda-title{left:33px;top:193px;font-size:32px;color:var(--white)}
.agenda-item{position:absolute;left:467px;width:265px;height:40px}
.agenda-icon{position:absolute;left:0;top:0}
.agenda-label{position:absolute;left:66px;top:5px;font-size:10.5px;font-weight:500;color:var(--ink);letter-spacing:.2px}
.agenda-line{position:absolute;left:66px;top:33px;width:196px;height:3px;background:#eeeeee}

/* footer */
.footer{position:absolute;left:0;top:398px;width:765px;height:32px}
.footer svg{position:absolute;left:0;top:0}
.footer-copy{position:absolute;left:35px;top:10px;font-size:11px;color:var(--white)}
.footer-brand{position:absolute;left:318px;top:2px}
.footer-page{position:absolute;right:35px;top:8px;font-size:10.5px;font-weight:700;color:var(--white)}

/* about */
.about-title{left:410px;top:36px;font-size:20px}
.about-rule{left:410px;top:75px;width:60px}
.about-copy{left:410px;top:94px;width:321px;font-size:10.5px;line-height:20px;color:var(--text);text-align:justify}
.about-copy p+p{margin-top:4px}
.checklist{position:absolute;left:410px;top:250px;list-style:none;font-size:9.5px;color:var(--text)}
.checklist li{height:23px;display:flex;align-items:flex-start;gap:11px}
.checklist svg{flex:none;margin-top:1px}

/* services */
.service-card{position:absolute;top:100px;width:217px;height:237px;background:var(--white);box-shadow:0 1px 6px rgba(0,0,0,.12)}
.service-card .photo{left:0;top:0;width:217px;height:152px}
.card-title{position:absolute;left:0;width:100%;text-align:center;font-size:11px;font-weight:500;color:var(--ink)}
.card-text{position:absolute;left:12px;right:12px;text-align:center;font-size:8.5px;line-height:14px;color:var(--text)}

/* team */
.team-card{position:absolute;top:99px;width:162px;height:243px;background:var(--white);box-shadow:0 1px 6px rgba(0,0,0,.12)}
.team-band{position:absolute;left:0;top:0;width:162px;height:86px}
.team-photo{position:absolute;left:29px;top:27px;width:104px;height:104px;border-radius:50%;border:3px solid var(--white);box-shadow:0 0 0 1px var(--blue-pale)}
.team-name{position:absolute;left:0;width:100%;top:143px;text-align:center;font-size:11.5px;font-weight:500}
.team-dash{position:absolute;left:73px;top:160px;width:16px;height:2px;background:var(--red)}
.team-role{position:absolute;left:0;width:100%;top:170px;text-align:center;font-size:6.5px;color:var(--text)}
.team-text{position:absolute;left:10px;right:10px;top:185px;text-align:center;font-size:7px;line-height:14px;color:var(--text)}

/* testimonials */
.quote-card{position:absolute;background:var(--white);border:1px solid #eee;border-radius:6px;box-shadow:0 1px 6px rgba(0,0,0,.08)}
.avatar{position:absolute;width:62px;height:62px;border-radius:50%;border:2px solid var(--white);box-shadow:0 1px 4px rgba(0,0,0,.2)}
.quote-name{position:absolute;font-size:11px;font-weight:500}
.quote-role{position:absolute;font-size:6px;color:var(--text)}
.quote-text{position:absolute;font-size:9.5px;line-height:17px;color:var(--text)}

/* experience */
.axis-label{position:absolute;left:20px;width:52px;text-align:right;font-family:"Open Sans",Arial,sans-serif;font-weight:600;font-size:15px;color:var(--red)}
.legend{position:absolute;top:340px;font-size:12px;display:flex;align-items:center;gap:12px}

/* closing */
.closing-bg{left:0;top:0;width:765px;height:430px;background:linear-gradient(180deg,#0a86cc 0%,#0b7dc4 55%,#1a6fb6 100%)}
.closing-title{left:0;width:100%;top:302px;text-align:center;font-size:40px;color:var(--white);letter-spacing:1px}
</style>
</head>
<body>
<div class="sheet">

  <!-- Cover -->
  <section class="slide col-l row-1">
    <div class="abs brand cover-brand">VANTORIS<span class="brand-mark"></span></div>
    <h1 class="abs heading cover-title">WELCOME TO VANTORIS</h1>
    <p class="abs cover-lead">Lorem ipsum dolor sit amet, consectetur adipiscing<br>elit, sed do eiusmod tempor incididunt.</p>
    <div class="abs cover-line"></div>
    <div class="abs cover-url">www.vantoris.com</div>
    <span class="social" style="left:140px"></span>
    <span class="social" style="left:168px"></span>
    <span class="social" style="left:196px"></span>
    <svg class="abs" style="left:0;top:0" width="765" height="430" viewBox="0 0 765 430">
      <polygon points="348,0 765,0 765,430 445,430" fill="#1f3a55" role="img" aria-label="Photo of two engineers with a laptop in a server room"/>
      <defs><linearGradient id="coverTone" x1="0" y1="0" x2="1" y2="1"><stop offset="0" stop-color="#3f6f95"/><stop offset="1" stop-color="#16283b"/></linearGradient></defs>
      <polygon points="348,0 765,0 765,430 445,430" fill="url(#coverTone)"/>
      <polygon points="350,88 365,88 445,430 428,430" fill="var(--red)"/>
    </svg>
  </section>

  <!-- Agenda -->
  <section class="slide col-r row-1">
    <div class="abs agenda-panel"></div>
    <div class="abs brand agenda-brand" style="color:#fff">VANTORIS<span class="brand-mark" style="background:#fff"></span></div>
    <h2 class="abs heading agenda-title">AGENDA</h2>
    <div class="photo" style="left:228px;top:0;width:246px;height:430px;background:linear-gradient(180deg,#b49a7f,#8a5a3c 60%,#6d4a35)" role="img" aria-label="Photo of a smiling businesswoman holding a tablet in an office"></div>
    <div class="agenda-item" style="top:90px">
      <svg class="agenda-icon" width="40" height="40" viewBox="0 0 40 40"><path d="M2 4 H20 A16 16 0 1 1 20 36 H8 Z" fill="var(--red)"/><circle cx="20" cy="18" r="8" fill="none" stroke="#fff" stroke-width="1.6"/><path d="M18 14 L22 18 L18 22" fill="none" stroke="#fff" stroke-width="1.6"/></svg>
      <span class="agenda-label">ABOUT US</span><span class="agenda-line"></span>
    </div>
    <div class="agenda-item" style="top:156px">
      <svg class="agenda-icon" width="40" height="40" viewBox="0 0 40 40"><path d="M2 4 H20 A16 16 0 1 1 20 36 H8 Z" fill="var(--red)"/><circle cx="20" cy="18" r="8" fill="none" stroke="#fff" stroke-width="1.6"/><path d="M18 14 L22 18 L18 22" fill="none" stroke="#fff" stroke-width="1.6"/></svg>
      <span class="agenda-label">OUR SERVICES</span><span class="agenda-line"></span>
    </div>
    <div class="agenda-item" style="top:227px">
      <svg class="agenda-icon" width="40" height="40" viewBox="0 0 40 40"><path d="M2 4 H20 A16 16 0 1 1 20 36 H8 Z" fill="var(--red)"/><circle cx="20" cy="18" r="8" fill="none" stroke="#fff" stroke-width="1.6"/><path d="M18 14 L22 18 L18 22" fill="none" stroke="#fff" stroke-width="1.6"/></svg>
      <span class="agenda-label">MEET THE&nbsp; TEAM</span><span class="agenda-line"></span>
    </div>
    <div class="agenda-item" style="top:291px">
      <svg class="agenda-icon" width="40" height="40" viewBox="0 0 40 40"><path d="M2 4 H20 A16 16 0 1 1 20 36 H8 Z" fill="var(--red)"/><circle cx="20" cy="18" r="8" fill="none" stroke="#fff" stroke-width="1.6"/><path d="M18 14 L22 18 L18 22" fill="none" stroke="#fff" stroke-width="1.6"/></svg>
      <span class="agenda-label">EXPERIENCE</span><span class="agenda-line"></span>
    </div>
  </section>

  <!-- About us -->
  <section class="slide col-l row-2">
    <div class="photo" style="left:34px;top:35px;width:348px;height:300px;background:linear-gradient(135deg,#5a6ee0 0%,#8a8f96 50%,#c9393e 100%)" role="img" aria-label="Collage of team photos in brand colours"></div>
    <h2 class="abs heading about-title">ABOUT US</h2>
    <div class="rule about-rule"></div>
    <div class="abs about-copy">
      <p>Lorem ipsum dolor sit amet, consectetur adipiscing elit, sed do eiusmod tempor incididunt ut labore et dolore magna aliqua. Ut enim ad minim veniam, quis nostrud exercitation ullamco laboris nisi ut aliquip ex ea commodo consequat.</p>
      <p>Duis aute irure dolor in reprehenderit in voluptate velit esse cillum dolore eu fugiat nulla pariatur. Excepteur sint occaecat cupidatat non proident, sunt in culpa qui officia.</p>
    </div>
    <ul class="checklist">
      <li><svg width="10" height="10" viewBox="0 0 10 10"><circle cx="5" cy="5" r="5" fill="var(--blue)"/><path d="M2.7 5.1 L4.3 6.6 L7.3 3.6" fill="none" stroke="#fff" stroke-width="1.3"/></svg>Lorem ipsum dolor sit amet, consectetur adipiscing</li>
      <li><svg width="10" height="10" viewBox="0 0 10 10"><circle cx="5" cy="5" r="5" fill="var(--blue)"/><path d="M2.7 5.1 L4.3 6.6 L7.3 3.6" fill="none" stroke="#fff" stroke-width="1.3"/></svg>Sed do eiusmod tempor incididunt ut labore et dolore</li>
      <li><svg width="10" height="10" viewBox="0 0 10 10"><circle cx="5" cy="5" r="5" fill="var(--blue)"/><path d="M2.7 5.1 L4.3 6.6 L7.3 3.6" fill="none" stroke="#fff" stroke-width="1.3"/></svg>Duis aute irure dolor in reprehenderit in voluptate velit esse cillum.</li>
      <li><svg width="10" height="10" viewBox="0 0 10 10"><circle cx="5" cy="5" r="5" fill="var(--blue)"/><path d="M2.7 5.1 L4.3 6.6 L7.3 3.6" fill="none" stroke="#fff" stroke-width="1.3"/></svg>Sed ut perspiciatis unde omnis iste natus error sit voluptatem.</li>
    </ul>
    <footer class="footer">
      <svg width="765" height="32" viewBox="0 0 765 32"><rect width="765" height="32" fill="var(--blue-deep)"/><polygon points="308,0 462,0 450,32 296,32" fill="#fff"/></svg>
      <span class="footer-copy">©&nbsp; 2024 Vantoris</span>
      <span class="brand footer-brand">VANTORIS<span class="brand-mark"></span></span>
      <span class="footer-page">Page:03</span>
    </footer>
  </section>

  <!-- Services -->
  <section class="slide col-r row-2">
    <h2 class="heading heading-center" style="top:32px">OUR SERVICES</h2>
    <div class="rule rule-center" style="top:75px"></div>
    <article class="service-card" style="left:40px">
      <div class="photo" style="background:linear-gradient(135deg,#d8a86a,#e9e4df 60%,#b9b2aa)" role="img" aria-label="Photo of two colleagues reviewing work at a laptop"></div>
      <h3 class="card-title" style="top:163px">Sed ut perspiciatis</h3>
      <p class="card-text" style="top:183px">Lorem ipsum dolor sit amet, consectetur adipiscing elit, sed do eiusmod tempor incididunt ut labore et dolore.</p>
    </article>
    <article class="service-card" style="left:274px">
      <div class="photo" style="background:linear-gradient(135deg,#cfd8df,#51606c 55%,#a9b5bf)" role="img" aria-label="Photo of a business team talking in a bright office"></div>
      <h3 class="card-title" style="top:163px">Sed ut perspiciatis</h3>
      <p class="card-text" style="top:183px">Lorem ipsum dolor sit amet, consectetur adipiscing elit, sed do eiusmod tempor incididunt ut labore et dolore.</p>
    </article>
    <article class="service-card" style="left:509px">
      <div class="photo" style="background:linear-gradient(135deg,#6f6a66,#c9ccce 55%,#8d8f8e)" role="img" aria-label="Photo of colleagues meeting around a glass table"></div>
      <h3 class="card-title" style="top:163px">Sed ut perspiciatis</h3>
      <p class="card-text" style="top:183px">Lorem ipsum dolor sit amet, consectetur adipiscing elit, sed do eiusmod tempor incididunt ut labore et dolore.</p>
    </article>
    <footer class="footer">
      <svg width="765" height="32" viewBox="0 0 765 32"><rect width="765" height="32" fill="var(--blue-deep)"/><polygon points="308,0 462,0 450,32 296,32" fill="#fff"/></svg>
      <span class="footer-copy">©&nbsp; 2024 Vantoris</span>
      <span class="brand footer-brand">VANTORIS<span class="brand-mark"></span></span>
      <span class="footer-page">Page:04</span>
    </footer>
  </section>

  <!-- Team -->
  <section class="slide col-l row-3">
    <h2 class="heading heading-center" style="top:33px">MEET THE TEAM</h2>
    <div class="rule rule-center" style="top:75px"></div>
    <article class="team-card" style="left:34px">
      <div class="team-band" style="background:var(--blue-deep)"></div>
      <div class="team-photo" style="background:linear-gradient(180deg,#c9ced3,#6e7377)" role="img" aria-label="Portrait of team member"></div>
      <h3 class="team-name">Liam Carver</h3><span class="team-dash"></span>
      <p class="team-role">(Sed ut perspiciatis)</p>
      <p class="team-text">Lorem ipsum dolor sit amet, tetur adipiscing elit, sed do eiusmod tempor incididunt ut.</p>
    </article>
    <article class="team-card" style="left:211px">
      <div class="team-band" style="background:var(--blue)"></div>
      <div class="team-photo" style="background:linear-gradient(180deg,#e4e7ea,#8fa6c0)" role="img" aria-label="Portrait of team member"></div>
      <h3 class="team-name">Owen Hale</h3><span class="team-dash"></span>
      <p class="team-role">(Sed ut perspiciatis)</p>
      <p class="team-text">Lorem ipsum dolor sit amet, tetur adipiscing elit, sed do eiusmod tempor incididunt ut.</p>
    </article>
    <article class="team-card" style="left:388px">
      <div class="team-band" style="background:var(--blue-deep)"></div>
      <div class="team-photo" style="background:linear-gradient(180deg,#5b5e61,#2e2f31)" role="img" aria-label="Portrait of team member"></div>
      <h3 class="team-name">Mira Stanton</h3><span class="team-dash"></span>
      <p class="team-role">(Sed ut perspiciatis)</p>
      <p class="team-text">Lorem ipsum dolor sit amet, tetur adipiscing elit, sed do eiusmod tempor incididunt ut.</p>
    </article>
    <article class="team-card" style="left:565px">
      <div class="team-band" style="background:var(--blue)"></div>
      <div class="team-photo" style="background:linear-gradient(180deg,#e7ddd0,#9fb3d0)" role="img" aria-label="Portrait of team member"></div>
      <h3 class="team-name">Clara Wendt</h3><span class="team-dash"></span>
      <p class="team-role">(Sed ut perspiciatis)</p>
      <p class="team-text">Lorem ipsum dolor sit amet, tetur adipiscing elit, sed do eiusmod tempor incididunt ut.</p>
    </article>
    <footer class="footer">
      <svg width="765" height="32" viewBox="0 0 765 32"><rect width="765" height="32" fill="var(--blue-deep)"/><polygon points="308,0 462,0 450,32 296,32" fill="#fff"/></svg>
      <span class="footer-copy">©&nbsp; 2024 Vantoris</span>
      <span class="brand footer-brand">VANTORIS<span class="brand-mark"></span></span>
      <span class="footer-page">Page:05</span>
    </footer>
  </section>

  <!-- Testimonials -->
  <section class="slide col-r row-3">
    <h2 class="heading heading-center" style="top:16px">CLIENT TESTIMONIALS</h2>
    <div class="rule rule-center" style="top:58px"></div>

    <article class="quote-card" style="left:34px;top:110px;width:220px;height:135px">
      <h3 class="quote-name" style="left:0;width:100%;text-align:center;top:40px">Owen Hale</h3>
      <p class="quote-role" style="left:0;width:100%;text-align:center;top:57px">Sed ut perspiciatis unde</p>
      <p class="quote-text" style="left:10px;right:10px;top:70px;text-align:center">Lorem ipsum dolor sit amet, consectetur adipiscing elit, sed do eiusmod tempor incididunt ut labore et dolore.</p>
    </article>
    <article class="quote-card" style="left:272px;top:110px;width:220px;height:135px">
      <h3 class="quote-name" style="left:0;width:100%;text-align:center;top:40px">Dalton</h3>
      <p class="quote-role" style="left:0;width:100%;text-align:center;top:57px">Sed ut perspiciatis unde</p>
      <p class="quote-text" style="left:10px;right:10px;top:70px;text-align:center">Lorem ipsum dolor sit amet, consectetur adipiscing elit, sed do eiusmod tempor incididunt ut labore et dolore.</p>
    </article>
    <article class="quote-card" style="left:510px;top:110px;width:220px;height:135px">
      <h3 class="quote-name" style="left:0;width:100%;text-align:center;top:40px">Ethan Marsh</h3>
      <p class="quote-role" style="left:0;width:100%;text-align:center;top:57px">Sed ut perspiciatis unde</p>
      <p class="quote-text" style="left:10px;right:10px;top:70px;text-align:center">Lorem ipsum dolor sit amet, consectetur adipiscing elit, sed do eiusmod tempor incididunt ut labore et dolore.</p>
    </article>
    <div class="avatar" style="left:112px;top:77px;background:linear-gradient(180deg,#b9c0c6,#2d3440)" role="img" aria-label="Client portrait"></div>
    <div class="avatar" style="left:351px;top:77px;background:linear-gradient(180deg,#9aa3ad,#3a4f6e)" role="img" aria-label="Client portrait"></div>
    <div class="avatar" style="left:589px;top:77px;background:linear-gradient(180deg,#6f7479,#4c6f86)" role="img" aria-label="Client portrait"></div>

    <article class="quote-card" style="left:65px;top:264px;width:305px;height:104px">
      <h3 class="quote-name" style="left:43px;top:12px">Noah Brennan</h3>
      <p class="quote-role" style="left:43px;top:28px">Sed ut perspiciatis unde</p>
      <p class="quote-text" style="left:43px;right:18px;top:41px;text-align:justify">Lorem ipsum dolor sit amet, consectetur adipiscing elit, sed do eiusmod tempor incididunt ut labore et dolore magna aliqua. Ut enim ad minim.</p>
    </article>
    <article class="quote-card" style="left:425px;top:264px;width:305px;height:104px">
      <h3 class="quote-name" style="left:43px;top:13px">Felix Rowan</h3>
      <p class="quote-role" style="left:43px;top:29px">Sed ut perspiciatis unde</p>
      <p class="quote-text" style="left:43px;right:10px;top:42px;text-align:justify">Lorem ipsum dolor sit amet, consectetur adipiscing elit, sed do eiusmod tempor incididunt ut labore et dolore magna aliqua, Ut enim ad minim veniam.</p>
    </article>
    <div class="avatar" style="left:32px;top:285px;background:linear-gradient(180deg,#cfe0ee,#3d6fa3)" role="img" aria-label="Client portrait"></div>
    <div class="avatar" style="left:393px;top:285px;background:linear-gradient(180deg,#e6e6e6,#3c6591)" role="img" aria-label="Client portrait"></div>

    <footer class="footer">
      <svg width="765" height="32" viewBox="0 0 765 32"><rect width="765" height="32" fill="var(--blue-deep)"/><polygon points="308,0 462,0 450,32 296,32" fill="#fff"/></svg>
      <span class="footer-copy">©&nbsp; 2024 Vantoris</span>
      <span class="brand footer-brand">VANTORIS<span class="brand-mark"></span></span>
      <span class="footer-page">Page:06</span>
    </footer>
  </section>

  <!-- Experience -->
  <section class="slide col-l row-4">
    <h2 class="heading heading-center" style="top:33px">EXPERIENCE</h2>
    <div class="rule rule-center" style="top:75px"></div>
    <span class="axis-label" style="top:92px">100%</span>
    <span class="axis-label" style="top:141px">75%</span>
    <span class="axis-label" style="top:190px">50%</span>
    <span class="axis-label" style="top:238px">25%</span>
    <span class="axis-label" style="top:286px">0%</span>
    <svg class="abs" style="left:0;top:0" width="765" height="330" viewBox="0 0 765 330" role="img" aria-label="Bar chart comparing experience levels">
      <g stroke="#e6e6e6" stroke-width="2">
        <line x1="88" y1="102" x2="730" y2="102"/><line x1="88" y1="151" x2="730" y2="151"/>
        <line x1="88" y1="200" x2="730" y2="200"/><line x1="88" y1="248" x2="730" y2="248"/>
        <line x1="88" y1="296" x2="730" y2="296"/>
      </g>
      <g fill="var(--track)">
        <rect x="117" y="102" width="35" height="208" rx="3"/><rect x="166" y="102" width="35" height="208" rx="3"/>
        <rect x="242" y="102" width="35" height="208" rx="3"/><rect x="291" y="102" width="35" height="208" rx="3"/>
        <rect x="366" y="102" width="35" height="208" rx="3"/><rect x="415" y="102" width="35" height="208" rx="3"/>
        <rect x="491" y="102" width="35" height="208" rx="3"/><rect x="540" y="102" width="35" height="208" rx="3"/>
        <rect x="615" y="102" width="35" height="208" rx="3"/><rect x="664" y="102" width="35" height="208" rx="3"/>
      </g>
      <g fill="var(--grey)">
        <rect x="117" y="244" width="35" height="66" rx="3"/><rect x="242" y="220" width="35" height="90" rx="3"/>
        <rect x="366" y="195" width="35" height="115" rx="3"/><rect x="491" y="180" width="35" height="130" rx="3"/>
        <rect x="615" y="170" width="35" height="140" rx="3"/>
      </g>
      <rect x="166" y="215" width="35" height="95" rx="3" fill="var(--blue)"/>
      <rect x="291" y="190" width="35" height="120" rx="3" fill="var(--blue-deep)"/>
      <rect x="415" y="170" width="35" height="140" rx="3" fill="var(--blue)"/>
      <rect x="540" y="145" width="35" height="165" rx="3" fill="var(--blue-deep)"/>
      <rect x="664" y="130" width="35" height="180" rx="3" fill="var(--blue)"/>
    </svg>
    <div class="legend" style="left:264px;color:var(--grey)"><svg width="20" height="20" viewBox="0 0 20 20"><circle cx="10" cy="10" r="7.5" fill="none" stroke="var(--grey)" stroke-width="4"/></svg>Experience</div>
    <div class="legend" style="left:403px;color:var(--blue-deep);font-weight:500"><svg width="20" height="20" viewBox="0 0 20 20"><circle cx="10" cy="10" r="7.5" fill="none" stroke="var(--blue-deep)" stroke-width="4"/></svg>Experience</div>
    <footer class="footer">
      <svg width="765" height="32" viewBox="0 0 765 32"><rect width="765" height="32" fill="var(--blue-deep)"/><polygon points="308,0 462,0 450,32 296,32" fill="#fff"/></svg>
      <span class="footer-copy">©&nbsp; 2024 Vantoris</span>
      <span class="brand footer-brand">VANTORIS<span class="brand-mark"></span></span>
      <span class="footer-page">Page:07</span>
    </footer>
  </section>

  <!-- Closing -->
  <section class="slide col-r row-4">
    <div class="abs closing-bg" role="img" aria-label="Blue-toned city skyline with a network world map and a businessman"></div>
    <h2 class="abs heading closing-title">THANK YOU!</h2>
  </section>

</div>
</body>
</html>
```